Web Developer Needs a Business Card Design

I need a personal business card design that represents me as a web developer for potential employers. I would like the background to be a dark color on the front for contrast with my logo and name. The back will have all my information along with a smaller version of the logo. I want something with a modern look and feel, not too conservative. This will be used for potential employers and freelance work.

Industry/Entity Type

Business

Contact Information for Business Card

Front should have my logo and name. The back should have all my personal information which would include: name: Tom Varulek, phone: 570-614-3098, email: tomvarulek@quillbox.net, website url: www.tomvarulek.net, logo, web developer.

Font styles to use
Sans Serif

Requirements
Must have
• Must include my logo. The color palette base color will be the logo color.

```html
<!DOCTYPE html>
<html lang="en">
<head>
<meta charset="utf-8">
<title>Tom Varulek — Business Card</title>
<link rel="stylesheet" href="https://fonts.googleapis.com/css2?family=Arimo:wght@400;700&display=swap">
<style>
  :root {
    --teal: #6cc8b6;
    --ink: #141414;
    --white: #ffffff;
    --backdrop: #e8e5e0;
  }
  * { box-sizing: border-box; margin: 0; padding: 0; }
  html, body {
    width: 1200px;
    height: 892px;
    overflow: hidden;
    background: var(--backdrop);
    font-family: "Arimo", Arial, sans-serif;
  }
  .canvas {
    width: 1200px;
    height: 892px;
    display: flex;
    align-items: center;
    justify-content: center;
    gap: 40px;
  }
  .card {
    width: 540px;
    height: 309px;
    position: relative;
    box-shadow: 0 6px 18px rgba(0,0,0,0.18);
  }
  .card--contact {
    background: var(--ink);
    border: 9px solid var(--teal);
    color: var(--white);
  }
  .card--brand {
    background: var(--teal);
    border: 9px solid var(--ink);
    color: var(--ink);
  }
  .mark {
    display: flex;
    align-items: center;
    gap: 10px;
    font-weight: 700;
    letter-spacing: 0.5px;
  }
  .mark__circle { border-radius: 50%; flex: none; }
  .card--contact .mark {
    position: absolute;
    top: 34px;
    left: 50%;
    transform: translateX(-50%);
    color: var(--teal);
    font-size: 20px;
  }
  .card--contact .mark__circle {
    width: 56px; height: 56px;
    border: 5px solid var(--teal);
  }
  .card--contact .rule {
    position: absolute;
    top: 118px;
    left: 60px;
    right: 60px;
    height: 1px;
    background: var(--white);
  }
  .card--contact .name {
    position: absolute;
    top: 136px;
    width: 100%;
    text-align: center;
    font-size: 40px;
    font-weight: 400;
    color: var(--teal);
  }
  .card--contact .role {
    position: absolute;
    top: 184px;
    width: 100%;
    text-align: center;
    font-size: 19px;
    font-weight: 700;
    letter-spacing: 0.5px;
  }
  .card--contact .details {
    position: absolute;
    bottom: 22px;
    width: 100%;
    text-align: center;
    font-size: 14px;
    letter-spacing: 0.3px;
  }
  .details .sep { margin: 0 8px; font-weight: 700; }
  .card--brand .mark {
    position: absolute;
    top: 62px;
    left: 50%;
    transform: translateX(-50%);
    font-size: 26px;
  }
  .card--brand .mark__circle {
    width: 110px; height: 110px;
    border: 9px solid var(--ink);
  }
  .card--brand .name {
    position: absolute;
    bottom: 40px;
    width: 100%;
    text-align: center;
    font-size: 34px;
    font-weight: 400;
  }
</style>
</head>
<body>
  <main class="canvas">
    <section class="card card--contact">
      <div class="mark"><span class="mark__circle"></span><span>Tom Varulek</span></div>
      <div class="rule"></div>
      <h1 class="name">Tom Varulek</h1>
      <p class="role">Web Developer</p>
      <p class="details">570-614-3098<span class="sep">|</span>tomvarulek@quillbox.net<span class="sep">|</span>www.tomvarulek.net</p>
    </section>
    <section class="card card--brand">
      <div class="mark"><span class="mark__circle"></span><span>Tom Varulek</span></div>
      <h2 class="name">Tom Varulek</h2>
    </section>
  </main>
</body>
</html>
```